Custom Cabinet Shop Needs a website design

Hi,
We need a website for a Custom Cabinet Shop and Cabinet parts manufacturing business.
The business has two sides to it. One side provides custom Kitchens, vanities, entertainment units, offices and what not to homeowners and contractors.
The 2nd side of the business provides built to order cabinet boxes and other parts required to put together a project to other cabinet shops, small contractors looking to install there own cabinets.
Website will need a Gallery to display work.
Color scheme to go well with logo.
current website is www.brambleoakcustomcabinets.com
being changed to www.brambleoak.ca
Logo Included in attached files.
Tagline "Joinery with Spirit"
Mission Statement "Our passion is to deliver inspired cabinetry solutions to suit all your needs, supported by our phenomenal star class customer service"
The website should convey quality and professionalism.
Thank you.
Homeowners/ Contractors
Entertainment

```html
<!DOCTYPE html>
<html lang="en">
<head>
<meta charset="utf-8">
<title>Bramble Oak Custom Cabinets</title>
<link href="https://fonts.googleapis.com/css2?family=Fira+Sans+Condensed:wght@300;400;600;700&display=swap" rel="stylesheet">
<style>
  :root {
    --orange: #f15a22;
    --ink: #1c1c1c;
    --text: #555;
    --nav: #555;
    --white: #fff;
    --footer: #232323;
    --page-tone-a: #d9d2c4;
    --page-tone-b: #c9bfae;
    --ceiling: #efe4d2;
    --wall: #d8c2a2;
    --wood-dark: #6e2410;
    --wood: #9a3519;
    --wood-light: #bd5f2f;
    --counter: #c9a878;
    --floor: #d6c8b4;
  }
  * { box-sizing: border-box; margin: 0; padding: 0; }
  html, body { width: 1200px; height: 1009px; overflow: hidden; }
  body {
    position: relative;
    font-family: "Fira Sans Condensed", sans-serif;
    background: linear-gradient(90deg, var(--page-tone-b), var(--page-tone-a) 30%, var(--page-tone-a) 70%, var(--page-tone-b));
  }
  .page-backdrop { position: absolute; left: 0; top: 108px; width: 1200px; height: 901px; }
  .top-band { position: absolute; left: 0; top: 0; width: 1200px; height: 108px; background: var(--white); }
  .site { position: absolute; left: 90px; top: 0; width: 1020px; height: 1009px; }

  .accent-rule { position: absolute; left: 0; top: 77px; width: 1020px; height: 6px; background: var(--orange); }

  .brand-tab { position: absolute; left: 20px; top: 0; width: 310px; height: 142px; }
  .brand-tab svg { position: absolute; inset: 0; }
  .brand-name {
    position: absolute; left: 26px; top: 50px;
    display: flex; align-items: center; gap: 10px;
    font-weight: 700; font-size: 36px; letter-spacing: 1px; color: var(--ink);
    text-transform: uppercase;
  }
  .brand-mark { width: 18px; height: 18px; background: var(--orange); }

  .main-nav { position: absolute; top: 24px; right: 6px; display: flex; }
  .main-nav a {
    display: block; height: 33px; line-height: 33px; padding: 0 16px;
    font-size: 18px; color: var(--nav); text-decoration: none; text-transform: uppercase;
    margin-left: 17px; position: relative;
  }
  .main-nav a + a::before {
    content: ""; position: absolute; left: -17px; top: -12px; width: 1px; height: 56px;
    background: linear-gradient(#fff, #ddd, #fff);
  }
  .main-nav a.is-current { background: var(--orange); color: var(--white); margin-left: 0; }

  .hero { position: absolute; left: 0; top: 83px; width: 1020px; height: 534px; }
  .hero-photo {
    position: absolute; inset: 0;
    background:
      radial-gradient(ellipse 60% 45% at 50% 48%, rgba(189,95,47,0.55), rgba(189,95,47,0) 70%),
      linear-gradient(90deg, rgba(70,20,8,0.45), rgba(70,20,8,0) 18%, rgba(70,20,8,0) 82%, rgba(70,20,8,0.45)),
      linear-gradient(180deg, var(--ceiling) 0%, var(--wall) 14%, var(--wood) 24%, var(--wood-dark) 45%, var(--wood-light) 58%, var(--counter) 62%, var(--wood) 68%, var(--wood-dark) 88%, var(--floor) 100%);
  }
  .hero-card {
    position: absolute; left: 578px; top: 183px; width: 442px; height: 151px;
    background: rgba(255,255,255,0.86);
    padding: 13px 18px 0 29px;
  }
  .hero-title {
    font-weight: 300; font-size: 47px; line-height: 46px; color: var(--ink);
    text-transform: uppercase; letter-spacing: -1.2px; white-space: nowrap;
  }
  .hero-title strong { font-weight: 600; color: var(--orange); }
  .hero-text { margin-top: 7px; font-size: 13.5px; line-height: 20px; color: #333; letter-spacing: -0.35px; }
  .btn {
    display: inline-flex; align-items: center; gap: 8px;
    background: var(--orange); color: var(--white); text-decoration: none;
    font-weight: 400;
  }
  .hero-btn { position: absolute; left: 608px; top: 321px; height: 33px; padding: 0 16px 0 19px; font-size: 18px; }

  .features { position: absolute; left: 0; top: 617px; width: 1020px; height: 290px; background: var(--white); }
  .feature { position: absolute; top: 46px; }
  .feature-title {
    height: 20px; border-left: 7px solid var(--orange); padding-left: 12px;
    font-weight: 400; font-size: 19px; line-height: 22px; color: var(--orange); text-transform: uppercase;
  }
  .feature-body {
    margin-top: 25px; border-left: 4px dotted #ccc; padding: 16px 0 0 15px;
    font-size: 13px; line-height: 22px; color: var(--text); letter-spacing: -0.3px;
  }
  .feature-about { left: 21px; width: 296px; }
  .feature-about .feature-body { height: 150px; }
  .feature-materials { left: 346px; width: 291px; }
  .feature-materials .feature-body { height: 150px; }
  .feature-btn { position: absolute; right: 0; top: 158px; height: 28px; padding: 0 14px 0 16px; font-size: 14px; }
  .feature-gallery { left: 668px; width: 332px; }
  .gallery-arrows { position: absolute; right: 0; top: 1px; display: flex; gap: 2px; }
  .gallery-arrows span { width: 17px; height: 17px; display: block; }
  .gallery-arrows .prev { background: #999; }
  .gallery-arrows .next { background: #222; }
  .gallery-frame {
    margin: 24px 0 0 24px; width: 308px; height: 145px; border: 1px solid #ddd; padding: 4px;
    box-shadow: 0 0 2px rgba(0,0,0,0.15);
  }
  .gallery-photo {
    width: 100%; height: 100%;
    background:
      linear-gradient(180deg, rgba(0,0,0,0) 55%, rgba(120,80,50,0.7) 75%, rgba(90,60,40,0.9) 100%),
      linear-gradient(90deg, #2a2626, #3a3232 35%, #5a4a3e 65%, #7a6652);
  }

  .site-footer { position: absolute; left: 0; top: 907px; width: 1020px; height: 102px; background: var(--footer); }
  .footer-brand {
    position: absolute; left: 24px; top: 37px; display: flex; align-items: center; gap: 9px;
    font-weight: 700; font-size: 28px; color: var(--white); letter-spacing: 1px; text-transform: uppercase;
  }
  .footer-brand .brand-mark { width: 15px; height: 15px; }
  .footer-nav { position: absolute; right: 21px; top: 25px; display: flex; font-size: 15px; }
  .footer-nav a { color: var(--white); text-decoration: none; }
  .footer-nav span { color: var(--white); margin: 0 13px; }
  .copyright { position: absolute; right: 21px; top: 65px; font-size: 13px; color: var(--white); letter-spacing: -0.2px; }
</style>
</head>
<body>
  <div class="page-backdrop" role="img" aria-label="Softly blurred photo of a bright kitchen interior"></div>
  <div class="top-band"></div>

  <div class="site">
    <div class="accent-rule"></div>

    <section class="hero">
      <div class="hero-photo" role="img" aria-label="Photo of a large cherry wood custom kitchen with glass-front upper cabinets, a carved central island with wine rack and a marble floor"></div>
      <div class="hero-card">
        <h1 class="hero-title">Joinery with <strong>Spirit</strong></h1>
        <p class="hero-text">Lorem ipsum dolor sit amet consectetur adipscing elit do eiusmod tempor incididunt ut labore et dolore magna aliqua enim ad minim veniam is quis exercitation ullamco laboris aliquip.</p>
      </div>
      <a class="btn hero-btn" href="#">Read More
        <svg width="9" height="13" viewBox="0 0 9 13"><path d="M2 1.5l5 5-5 5" fill="none" stroke="#fff" stroke-width="2"/></svg>
      </a>
    </section>

    <div class="brand-tab">
      <svg width="310" height="142" viewBox="0 0 310 142"><path d="M0 77H310V142L160 124 0 142Z" fill="#fff"/></svg>
      <div class="brand-name"><span class="brand-mark"></span>Bramble Oak</div>
    </div>

    <nav class="main-nav">
      <a class="is-current" href="#">Home</a>
      <a href="#">Gallery</a>
      <a href="#">Services</a>
      <a href="#">Warranty</a>
      <a href="#">Contact</a>
    </nav>

    <section class="features">
      <article class="feature feature-about">
        <h2 class="feature-title">About Us</h2>
        <p class="feature-body">Lorem ipsum dolor sit amet, consectetur adipiscing elit, sed do eiusmod tempor incididunt ut labore et dolore magna aliqua. Ut enim ad minim veniam, quis nostrud exercitation ullamco laboris nisi ut aliquip ex ea commodo consequat. Duis aute irure dolor in reprehenderit in voluptate velit esse</p>
      </article>

      <article class="feature feature-materials">
        <h2 class="feature-title">Finest Quality Materials</h2>
        <p class="feature-body">Lorem ipsum dolor sit amet, consectetur adipiscing elit, sed do eiusmod tempor incididunt ut labore et dolore magna aliqua enim ad minim veniam is quis exercitation ullamco.</p>
        <a class="btn feature-btn" href="#">Read More
          <svg width="8" height="11" viewBox="0 0 8 11"><path d="M2 1.5l4 4-4 4" fill="none" stroke="#fff" stroke-width="1.8"/></svg>
        </a>
      </article>

      <article class="feature feature-gallery">
        <h2 class="feature-title">Our Gallery</h2>
        <div class="gallery-arrows">
          <span class="prev"><svg width="17" height="17" viewBox="0 0 17 17"><path d="M10 5l-3.5 3.5L10 12" fill="none" stroke="#fff" stroke-width="1.6"/></svg></span>
          <span class="next"><svg width="17" height="17" viewBox="0 0 17 17"><path d="M7 5l3.5 3.5L7 12" fill="none" stroke="#fff" stroke-width="1.6"/></svg></span>
        </div>
        <div class="gallery-frame">
          <div class="gallery-photo" role="img" aria-label="Photo of a dark kitchen with a live-edge bar counter, pendant lights and stools"></div>
        </div>
      </article>
    </section>

    <footer class="site-footer">
      <div class="footer-brand"><span class="brand-mark"></span>Bramble Oak</div>
      <nav class="footer-nav">
        <a href="#">Home</a><span>|</span>
        <a href="#">Gallery</a><span>|</span>
        <a href="#">Services</a><span>|</span>
        <a href="#">Warranty</a><span>|</span>
        <a href="#">Contact</a>
      </nav>
      <p class="copyright">Copyright © 2015 . Bramble Oak . All Rights Reserved.</p>
    </footer>
  </div>
</body>
</html>
```